Specialised investor in e-mobility and energy wants business card design

We need a business card design that fits our existing corporate design. <The look and feel must be 'sharp'/'clean', dynamic, communicate momentum, professionalism etc (as one would imagine from a firm in the financial sector). We like the idea of a reverse-side of the card that includes the logo, and the name and contact details on the other. We expect the deliverable to be whatever format might be required to be able to get cards printed directly by a service such as kelmo press. Our website is www.zub.capital

```html
<!DOCTYPE html>
<html lang="en">
<head>
<meta charset="utf-8">
<title>ZUB Capital – Business Card</title>
<link rel="stylesheet" href="https://fonts.googleapis.com/css2?family=Questrial&family=Mulish:wght@800&display=swap">
<style>
  :root {
    --forest: #2d4a21;
    --leaf: #7fac4a;
    --paper: #f5f5f7;
    --backdrop: #e4e4e4;
    --ink-light: #ffffff;
  }
  * { margin: 0; padding: 0; box-sizing: border-box; }
  html, body { width: 1200px; height: 1200px; overflow: hidden; }
  body {
    background: var(--backdrop);
    position: relative;
    font-family: "Questrial", "Century Gothic", sans-serif;
  }
  .card {
    position: absolute;
    left: 262px;
    width: 686px;
    height: 392px;
    border-radius: 22px;
    overflow: hidden;
  }
  .card--front { top: 165px; background: var(--paper); }
  .card--back { top: 653px; background: var(--forest); }

  .wave { position: absolute; inset: 0; width: 100%; height: 100%; }

  .wordmark {
    position: absolute;
    white-space: nowrap;
    font-family: "Questrial", "Century Gothic", sans-serif;
    font-weight: 400;
    line-height: 1;
  }
  .card--front .wordmark {
    right: 48px;
    top: 66px;
    font-size: 54px;
    color: var(--forest);
  }
  .card--back .wordmark {
    left: 50%;
    top: 50%;
    transform: translate(-50%, -50%);
    font-size: 72px;
    color: var(--ink-light);
  }

  .contact {
    position: absolute;
    left: 41px;
    top: 191px;
    color: var(--ink-light);
  }
  .contact__name {
    font-family: "Mulish", "Century Gothic", sans-serif;
    font-weight: 800;
    font-size: 22px;
    letter-spacing: 0.5px;
    color: var(--leaf);
    line-height: 1;
  }
  .contact__role { font-size: 15.5px; margin-top: 5px; }
  .contact__city { font-size: 16.5px; margin-top: 13px; }
  .contact__line {
    display: flex;
    align-items: center;
    gap: 12px;
    font-size: 16.5px;
    margin-top: 6px;
  }
  .contact__line:first-of-type { margin-top: 11px; }
  .contact__icon { width: 14px; height: 14px; fill: var(--leaf); flex: none; }
  .contact__web {
    font-family: "Mulish", "Century Gothic", sans-serif;
    font-weight: 800;
    font-size: 15.5px;
    color: var(--leaf);
    margin-top: 14px;
  }
</style>
</head>
<body>
  <section class="card card--front">
    <svg class="wave" viewBox="0 0 800 457" preserveAspectRatio="none" aria-hidden="true">
      <path d="M25 180 Q190 118 430 172 Q650 228 800 376 L800 457 L0 457 Z" fill="var(--leaf)"/>
      <path d="M0 188 Q200 140 440 202 Q650 262 800 432 L800 457 L0 457 Z" fill="var(--forest)" stroke="#ffffff" stroke-width="2.5"/>
    </svg>
    <div class="wordmark">ZUB Capital</div>
    <div class="contact">
      <div class="contact__name">PETER HALLWORTH</div>
      <div class="contact__role">Managing Director</div>
      <div class="contact__city">Basel, Switzerland</div>
      <div class="contact__line">
        <svg class="contact__icon" viewBox="0 0 24 24" aria-hidden="true"><path d="M6.6 10.8a15 15 0 0 0 6.6 6.6l2.2-2.2a1 1 0 0 1 1-.25 11.4 11.4 0 0 0 3.6.57 1 1 0 0 1 1 1V20a1 1 0 0 1-1 1A17 17 0 0 1 3 4a1 1 0 0 1 1-1h3.5a1 1 0 0 1 1 1c0 1.25.2 2.45.57 3.57a1 1 0 0 1-.25 1z"/></svg>
        <span>+41 70000 1234</span>
      </div>
      <div class="contact__line">
        <svg class="contact__icon" viewBox="0 0 24 24" aria-hidden="true"><path d="M2 5h20v14H2z M2 5l10 7 10-7" /><path d="M3 6l9 6.3L21 6" fill="none" stroke="var(--forest)" stroke-width="1.6"/></svg>
        <span>peter@zub.capital</span>
      </div>
      <div class="contact__web">www.zub.capital</div>
    </div>
  </section>

  <section class="card card--back">
    <div class="wordmark">ZUB Capital</div>
  </section>
</body>
</html>
```